QuillVane needs a dashboard page designed

Redesign the dashboard shown in the provided images.

There are two images:
- dashboard.png
- dashboard-expanded.png

NOTE: The vocabulary navigation on the left will be a very long list of words 100s, so keep that in mind when you're designing both the vocab navigation and the expanded vocab popup.

In the dashboard.png picture, there needs to be a progress chart showing the word progress like the following: review 1(show it as completed) -> review 2(show the user they are here) -> review 3(unvisited) -> review 4(unvisited)

The do-not-design-this-page.png image is for your reference only. It is not to be designed. Use it to understand the overall look and feel of the website to help you create the best dashboard page possible.
Updates

Need extra days to review

Industry/Entity Type

Education English learning

Number of Pages Required

1 page

Requirements
Must have
• The main navigation and main header cannot change between pages. See the do-not-design page for the main navigateion and header.
Should not have
• Do not add a person profile. We will not have images of our users. Keep the icons in the main navigation as they are.

```html
<!DOCTYPE html>
<html lang="en">
<head>
<meta charset="utf-8">
<title>QuillVane – Dashboard</title>
<link href="https://fonts.googleapis.com/css2?family=Lato:wght@400;700;900&display=swap" rel="stylesheet">
<style>
:root{
  --teal:#10a393;
  --navy:#134f6f;
  --ink:#1a4a6b;
  --text:#333c44;
  --muted:#8a9299;
  --line:#e3e8ec;
  --ring-bg:#e7e7e7;
  --page:#f3f4f6;
  --band-1:#a9dbf3;
  --band-2:#b6e2f6;
  --band-3:#cceaf7;
  --band-4:#def1fa;
  --veil:rgba(18,80,112,.58);
}
*{box-sizing:border-box;margin:0;padding:0}
html,body{width:1200px;height:520px;overflow:hidden}
body{background:var(--page);font-family:'Lato',sans-serif;color:var(--text);position:relative}
.screen{position:absolute;top:29px;width:1194px;height:991px;transform:scale(.4667);transform-origin:0 0;background:#fff;overflow:hidden;border-radius:30px 0 0 30px}
.screen--main{left:28px}
.screen--expanded{left:616px}
.abs{position:absolute}

/* rails */
.icon-rail{left:0;top:0;width:60px;height:991px;background:var(--teal);border-radius:30px 0 0 30px}
.rail-item{position:absolute;left:0;width:40px;display:flex;flex-direction:column;align-items:center;color:#fff;font-size:9px;line-height:1.5;text-align:center}
.brand{left:36px;top:0;width:214px;height:80px;background:var(--navy);border-radius:0 0 26px 0;color:#fff;font-weight:900;font-size:28px;display:flex;align-items:center;justify-content:center}
.brand-joint{left:36px;top:70px;width:30px;height:60px;background:var(--navy)}
.filter-bar{left:57px;top:80px;width:193px;height:40px;background:#fff;border-radius:20px 0 0 20px;display:flex;align-items:center;padding:0 14px 0 20px;justify-content:space-between;font-size:11px}
.filter-select{color:var(--teal);font-weight:700;font-size:13px;display:flex;gap:40px;align-items:center}
.filter-expand{color:var(--text);display:flex;gap:5px;align-items:center}
.vocab-nav{left:36px;top:120px;width:214px;height:871px;background:var(--navy);border-radius:0 24px 24px 0;color:#fff}
.group{position:absolute;left:20px;display:flex;align-items:center;gap:6px;font-weight:700;font-size:12.5px}
.word{position:absolute;left:44px;font-size:8.5px}
.word--active{color:var(--teal)}
.help{width:8px;height:8px;border-radius:50%;background:#fff;color:var(--navy);font-size:7px;display:inline-flex;align-items:center;justify-content:center;font-weight:900}

/* header */
.app-title{left:284px;top:16px;color:var(--teal);font-size:17px;font-weight:700}
.header-line{left:250px;top:52px;width:944px;height:1px;background:var(--line)}
.user{left:1042px;top:14px;display:flex;align-items:center;gap:6px;font-size:8px}
.avatar{width:28px;height:28px;border-radius:50%;background:linear-gradient(135deg,#c9a98f,#6e7a86)}
.header-icon{top:20px}

/* cards */
.card{position:absolute;border:1px solid var(--line);border-radius:12px;background:#fff;box-shadow:0 1px 3px rgba(0,0,0,.04)}
.card-title{position:absolute;left:22px;color:var(--ink);font-size:14.5px;font-weight:700}
.card-copy{position:absolute;left:22px;right:40px;font-size:10px;line-height:17px;color:var(--text)}
.progress-card{left:346px;top:70px;width:762px;height:228px}
.progress-title{position:absolute;top:26px;width:100%;text-align:center;color:var(--ink);font-size:14px;font-weight:700}
.ring{position:absolute;top:58px;width:124px;text-align:center}
.ring svg{display:block;margin:0 auto}
.ring-value{position:absolute;top:42px;width:100%;font-size:15px}
.ring-sub{position:absolute;top:62px;width:100%;font-size:9px;color:var(--muted)}
.ring-label{margin-top:14px;font-size:13px;color:var(--text)}
.current-word{left:672px;top:318px;font-size:16px;font-weight:700;color:var(--ink);display:flex;gap:6px;align-items:center}
.start-btn{left:576px;top:354px;width:294px;height:39px;border-radius:20px;background:var(--teal);color:#fff;font-size:13.5px;font-weight:700;display:flex;align-items:center;justify-content:center;gap:8px}

/* chart */
.curve-chart{position:absolute;left:18px;top:61px;width:869px;height:193px}
.band{position:absolute;left:0;width:100%;font-size:8px;color:#4a6272;padding-left:10px;display:flex;align-items:center;letter-spacing:.3px}
.bar{position:absolute;width:17px;background:var(--teal);bottom:0}
.tag{position:absolute;width:50px;height:17px;border-radius:9px;background:var(--navy);color:#fff;font-size:8px;font-weight:700;display:flex;align-items:center;justify-content:center}
.axis{position:absolute;left:68px;right:24px;top:264px;display:flex;justify-content:space-between;font-size:7px;color:#555}
.axis-title{position:absolute;top:281px;width:100%;text-align:center;font-size:10px;color:var(--ink)}
.chart-credit{position:absolute;right:10px;top:284px;font-size:7px;color:#555}

/* expanded overlay */
.veil{left:0;top:0;width:1194px;height:991px;background:var(--veil)}
.vocab-popup{left:288px;top:161px;width:620px;height:209px;background:#fff;border-radius:10px}
.popup-select{position:absolute;left:20px;top:19px;width:97px;height:28px;border-radius:14px;background:#f1f3f5;color:var(--teal);font-weight:700;font-size:12px;display:flex;align-items:center;justify-content:space-between;padding:0 12px}
.popup-close{position:absolute;right:18px;top:18px}
.popup-group{position:absolute;left:28px;display:flex;align-items:center;gap:6px;color:var(--ink);font-weight:700;font-size:12.5px}
.popup-word{position:absolute;left:52px;font-size:8px;color:var(--text)}
.popup-row{position:absolute;left:52px;right:20px;top:197px;display:flex;justify-content:space-between;font-size:8px}
.popup-help{width:8px;height:8px;border-radius:50%;background:var(--teal);color:#fff;font-size:7px;display:inline-flex;align-items:center;justify-content:center;font-weight:900}
</style>
</head>
<body>

<!-- ========== Dashboard ========== -->
<section class="screen screen--main">
  <div class="abs icon-rail">
    <div class="rail-item" style="top:88px">
      <svg width="20" height="18" viewBox="0 0 20 18"><path d="M10 1 1 9h3v8h4v-5h4v5h4V9h3z" fill="#fff"/></svg>
      <span style="margin-top:6px">Word<br>Mentor</span>
    </div>
    <div class="rail-item" style="top:166px"><svg width="18" height="20" viewBox="0 0 18 20"><path d="M9 1a6 6 0 0 0-6 6c0 4.5 6 10 6 10s6-5.5 6-10a6 6 0 0 0-6-6zm0 8a2 2 0 1 1 0-4 2 2 0 0 1 0 4z" fill="#fff"/><rect x="2" y="17" width="14" height="2" rx="1" fill="#fff"/></svg></div>
    <div class="rail-item" style="top:206px"><svg width="20" height="18" viewBox="0 0 20 18"><rect x="1" y="5" width="18" height="12" rx="2" fill="#fff"/><path d="M7 5V2h6v3" stroke="#fff" stroke-width="2" fill="none"/><rect x="1" y="10" width="18" height="1.5" fill="#10a393"/></svg></div>
  </div>
  <div class="abs brand-joint"></div>
  <div class="abs brand">QuillVane</div>
  <div class="abs filter-bar">
    <span class="filter-select">All <svg width="9" height="6" viewBox="0 0 9 6"><path d="m1 1 3.5 3.5L8 1" stroke="#333" fill="none" stroke-width="1.3"/></svg></span>
    <span class="filter-expand">Expand <svg width="10" height="10" viewBox="0 0 10 10"><path d="M4 1H1v8h8V6M6 1h3v3M9 1 4.5 5.5" stroke="#10a393" fill="none" stroke-width="1.2"/></svg></span>
  </div>
  <nav class="abs vocab-nav">
    <div class="group" style="top:19px"><svg width="18" height="18" viewBox="0 0 18 18"><circle cx="9" cy="10" r="6.5" stroke="#fff" fill="none" stroke-width="1.4"/><path d="M9 6v4l3 2M7 1h4" stroke="#fff" fill="none" stroke-width="1.4"/></svg>Short-Term Memory <span class="help">?</span></div>
    <div class="word word--active" style="top:42px">Grab</div>
    <div class="group" style="top:61px"><svg width="18" height="18" viewBox="0 0 18 18"><rect x="4" y="4" width="10" height="10" stroke="#fff" fill="none" stroke-width="1.4"/><rect x="7" y="7" width="4" height="4" fill="#fff"/><path d="M7 1v3M11 1v3M7 14v3M11 14v3M1 7h3M1 11h3M14 7h3M14 11h3" stroke="#fff" stroke-width="1.2"/></svg>Working Memory <span class="help">?</span></div>
    <div class="word" style="top:86px">Cool Down</div>
    <div class="word" style="top:107px">Crave</div>
    <div class="word" style="top:128px">Go For</div>
    <div class="word" style="top:149px">Go-To</div>
    <div class="word" style="top:171px">In The Mood For</div>
    <div class="word" style="top:192px">Sip</div>
    <div class="word" style="top:213px">Soothing</div>
    <div class="group" style="top:231px"><svg width="16" height="18" viewBox="0 0 16 18"><rect x="2" y="8" width="12" height="9" rx="1.5" stroke="#fff" fill="none" stroke-width="1.4"/><path d="M5 8V5a3 3 0 0 1 6 0" stroke="#fff" fill="none" stroke-width="1.4"/></svg>Long-Term Memory <span class="help">?</span></div>
    <div class="word" style="top:257px">Give It A Try</div>
  </nav>

  <div class="abs app-title">Word Mentor</div>
  <div class="abs user"><div class="avatar" role="img" aria-label="User avatar"></div>R. Okafor</div>
  <svg class="abs header-icon" style="left:1128px" width="14" height="16" viewBox="0 0 14 16"><path d="M7 1a4.5 4.5 0 0 0-4.5 4.5V10L1 12h12l-1.5-2V5.5A4.5 4.5 0 0 0 7 1z" fill="#134f6f"/><circle cx="7" cy="14" r="1.8" fill="#134f6f"/></svg>
  <svg class="abs header-icon" style="left:1158px" width="16" height="16" viewBox="0 0 16 16"><circle cx="8" cy="8" r="5" fill="none" stroke="#134f6f" stroke-width="3.4" stroke-dasharray="2.6 1.6"/><circle cx="8" cy="8" r="4" fill="#134f6f"/><circle cx="8" cy="8" r="1.7" fill="#fff"/></svg>
  <div class="abs header-line"></div>

  <div class="card progress-card">
    <div class="progress-title">Review Progress</div>
    <div class="ring" style="left:30px">
      <svg width="124" height="124" viewBox="0 0 124 124"><circle cx="62" cy="62" r="54" fill="none" stroke="var(--teal)" stroke-width="13"/></svg>
      <div class="ring-value" style="color:var(--teal)">100%</div><div class="ring-sub">Progress</div>
      <div class="ring-label">Completed</div>
    </div>
    <div class="ring" style="left:220px">
      <svg width="124" height="124" viewBox="0 0 124 124"><circle cx="62" cy="62" r="54" fill="none" stroke="var(--ring-bg)" stroke-width="13"/><circle cx="62" cy="62" r="54" fill="none" stroke="var(--navy)" stroke-width="13" stroke-dasharray="169.6 339.3" transform="rotate(180 62 62)"/></svg>
      <div class="ring-value" style="color:var(--navy)">50%</div><div class="ring-sub">Progress</div>
      <div class="ring-label">Current</div>
    </div>
    <div class="ring" style="left:412px">
      <svg width="124" height="124" viewBox="0 0 124 124"><circle cx="62" cy="62" r="54" fill="none" stroke="var(--ring-bg)" stroke-width="13"/></svg>
      <div class="ring-value" style="color:var(--muted)">0%</div><div class="ring-sub">Progress</div>
      <div class="ring-label">Unvisited</div>
    </div>
    <div class="ring" style="left:602px">
      <svg width="124" height="124" viewBox="0 0 124 124"><circle cx="62" cy="62" r="54" fill="none" stroke="var(--ring-bg)" stroke-width="13"/></svg>
      <div class="ring-value" style="color:var(--muted)">0%</div><div class="ring-sub">Progress</div>
      <div class="ring-label">Unvisited</div>
    </div>
  </div>
  <div class="abs current-word">Grab <svg width="15" height="15" viewBox="0 0 24 24"><path d="m12 2 3 6.5 7 .8-5.2 4.8 1.5 7L12 17.6 5.7 21.1l1.5-7L2 9.3l7-.8z" fill="#f5c518"/></svg></div>
  <div class="abs start-btn"><svg width="10" height="11" viewBox="0 0 10 11"><path d="M1 1v9l8-4.5z" fill="#fff"/></svg>Start Vocabulary Review Exercise 3</div>

  <div class="card" style="left:271px;top:416px;width:905px;height:124px">
    <div class="card-title" style="top:22px">Learning Curve Graph</div>
    <p class="card-copy" style="top:50px">The word "grab" is most commonly used as a verb, meaning to take something quickly or suddenly. Imagine you're running late for school. You don't have time for breakfast, so you quickly grab an apple from the kitchen and rush out the door. As you reach the bus stop, your friend waves and says, "Hey! Let's grab a coffee aller class" Later, when you sit down, your phone starts ringing. You grab it from your brag and answer.</p>
  </div>

  <div class="card" style="left:271px;top:561px;width:905px;height:315px">
    <div class="card-title" style="top:22px">Learning Curve Graph</div>
    <div class="curve-chart">
      <div class="band" style="top:0;height:53px;background:var(--band-1)">Long-Term Memory</div>
      <div class="band" style="top:53px;height:82px;background:var(--band-2)">Working Memory</div>
      <div class="band" style="top:135px;height:28px;background:var(--band-3)">Short-Term Memory</div>
      <div class="band" style="top:163px;height:30px;background:var(--band-4)">Forgotten Memory</div>
      <svg class="abs" style="left:0;top:0" width="869" height="193" viewBox="0 0 869 193"><path d="M211 56C300 50 377 100 377 193M132 132C175 128 198 160 200 193" fill="none" stroke="#2b3b47" stroke-width="1" stroke-dasharray="3 3"/><line x1="0" y1="193" x2="869" y2="193" stroke="#c8d3da"/></svg>
      <div class="bar" style="left:123px;height:63px"></div>
      <div class="bar" style="left:203px;height:135px"></div>
      <div class="tag" style="left:85px;top:123px">May 18</div>
      <div class="tag" style="left:160px;top:51px">May 19</div>
    </div>
    <div class="axis"><span>18 May</span><span>12:00</span><span>19 May</span><span>12:00</span><span>20 May</span><span>12:00</span><span>21 May</span><span>12:00</span><span>22 May</span><span>12:00</span><span>23 May</span><span>12:00</span><span>24 May</span><span>12:00</span><span>25 May</span><span>12:00</span><span>26 May</span><span>12:00</span><span>27 May</span><span>12:00</span><span>28 …</span></div>
    <div class="axis-title">Date Range</div>
    <div class="chart-credit">ChartKit.io</div>
  </div>

  <div class="card" style="left:271px;top:896px;width:905px;height:140px">
    <div class="card-title" style="top:22px">Word Mentor Learning Analysis</div>
    <p class="card-copy" style="top:50px;right:100px">Lorem ipsum dolor sit amet, consectetur adipiscing elit, sed do eiusmod tempor incididunt ut labore et dolore magna aliqua. Ut enim ad minim veniam, quis nostrud exercitation ullamco laboris nisi ut aliquip ex ea commodo consequat. Duis aute irure dolor in reprehenderit in voluptate velit esse cillum dolore eu fugiat nulla pariatur. Excepteur sint occaecat cupidatat non proident, sunt in culpa qui officia deserunt mollit anim id est laborum.</p>
  </div>
</section>

<!-- ========== Dashboard with expanded vocabulary ========== -->
<section class="screen screen--expanded">
  <div class="abs icon-rail">
    <div class="rail-item" style="top:88px">
      <svg width="20" height="18" viewBox="0 0 20 18"><path d="M10 1 1 9h3v8h4v-5h4v5h4V9h3z" fill="#fff"/></svg>
      <span style="margin-top:6px">Word<br>Mentor</span>
    </div>
    <div class="rail-item" style="top:166px"><svg width="18" height="20" viewBox="0 0 18 20"><path d="M9 1a6 6 0 0 0-6 6c0 4.5 6 10 6 10s6-5.5 6-10a6 6 0 0 0-6-6zm0 8a2 2 0 1 1 0-4 2 2 0 0 1 0 4z" fill="#fff"/><rect x="2" y="17" width="14" height="2" rx="1" fill="#fff"/></svg></div>
    <div class="rail-item" style="top:206px"><svg width="20" height="18" viewBox="0 0 20 18"><rect x="1" y="5" width="18" height="12" rx="2" fill="#fff"/><path d="M7 5V2h6v3" stroke="#fff" stroke-width="2" fill="none"/><rect x="1" y="10" width="18" height="1.5" fill="#10a393"/></svg></div>
  </div>
  <div class="abs brand-joint"></div>
  <div class="abs brand">QuillVane</div>
  <div class="abs filter-bar">
    <span class="filter-select">All <svg width="9" height="6" viewBox="0 0 9 6"><path d="m1 1 3.5 3.5L8 1" stroke="#333" fill="none" stroke-width="1.3"/></svg></span>
    <span class="filter-expand">Expand <svg width="10" height="10" viewBox="0 0 10 10"><path d="M4 1H1v8h8V6M6 1h3v3M9 1 4.5 5.5" stroke="#10a393" fill="none" stroke-width="1.2"/></svg></span>
  </div>
  <nav class="abs vocab-nav">
    <div class="group" style="top:19px"><svg width="18" height="18" viewBox="0 0 18 18"><circle cx="9" cy="10" r="6.5" stroke="#fff" fill="none" stroke-width="1.4"/><path d="M9 6v4l3 2M7 1h4" stroke="#fff" fill="none" stroke-width="1.4"/></svg>Short-Term Memory <span class="help">?</span></div>
    <div class="word word--active" style="top:42px">Grab</div>
    <div class="group" style="top:61px"><svg width="18" height="18" viewBox="0 0 18 18"><rect x="4" y="4" width="10" height="10" stroke="#fff" fill="none" stroke-width="1.4"/><rect x="7" y="7" width="4" height="4" fill="#fff"/><path d="M7 1v3M11 1v3M7 14v3M11 14v3M1 7h3M1 11h3M14 7h3M14 11h3" stroke="#fff" stroke-width="1.2"/></svg>Working Memory <span class="help">?</span></div>
    <div class="word" style="top:86px">Cool Down</div>
    <div class="word" style="top:107px">Crave</div>
    <div class="word" style="top:128px">Go For</div>
    <div class="word" style="top:149px">Go-To</div>
    <div class="word" style="top:171px">In The Mood For</div>
    <div class="word" style="top:192px">Sip</div>
    <div class="word" style="top:213px">Soothing</div>
    <div class="group" style="top:231px"><svg width="16" height="18" viewBox="0 0 16 18"><rect x="2" y="8" width="12" height="9" rx="1.5" stroke="#fff" fill="none" stroke-width="1.4"/><path d="M5 8V5a3 3 0 0 1 6 0" stroke="#fff" fill="none" stroke-width="1.4"/></svg>Long-Term Memory <span class="help">?</span></div>
    <div class="word" style="top:257px">Give It A Try</div>
  </nav>

  <div class="abs app-title">Word Mentor</div>
  <div class="abs user"><div class="avatar" role="img" aria-label="User avatar"></div>R. Okafor</div>
  <svg class="abs header-icon" style="left:1128px" width="14" height="16" viewBox="0 0 14 16"><path d="M7 1a4.5 4.5 0 0 0-4.5 4.5V10L1 12h12l-1.5-2V5.5A4.5 4.5 0 0 0 7 1z" fill="#134f6f"/><circle cx="7" cy="14" r="1.8" fill="#134f6f"/></svg>
  <svg class="abs header-icon" style="left:1158px" width="16" height="16" viewBox="0 0 16 16"><circle cx="8" cy="8" r="5" fill="none" stroke="#134f6f" stroke-width="3.4" stroke-dasharray="2.6 1.6"/><circle cx="8" cy="8" r="4" fill="#134f6f"/><circle cx="8" cy="8" r="1.7" fill="#fff"/></svg>
  <div class="abs header-line"></div>

  <div class="card progress-card">
    <div class="progress-title">Review Progress</div>
    <div class="ring" style="left:30px">
      <svg width="124" height="124" viewBox="0 0 124 124"><circle cx="62" cy="62" r="54" fill="none" stroke="var(--teal)" stroke-width="13"/></svg>
      <div class="ring-value" style="color:var(--teal)">100%</div><div class="ring-sub">Progress</div>
      <div class="ring-label">Completed</div>
    </div>
    <div class="ring" style="left:220px">
      <svg width="124" height="124" viewBox="0 0 124 124"><circle cx="62" cy="62" r="54" fill="none" stroke="var(--ring-bg)" stroke-width="13"/><circle cx="62" cy="62" r="54" fill="none" stroke="var(--navy)" stroke-width="13" stroke-dasharray="169.6 339.3" transform="rotate(180 62 62)"/></svg>
      <div class="ring-value" style="color:var(--navy)">50%</div><div class="ring-sub">Progress</div>
      <div class="ring-label">Current</div>
    </div>
    <div class="ring" style="left:412px">
      <svg width="124" height="124" viewBox="0 0 124 124"><circle cx="62" cy="62" r="54" fill="none" stroke="var(--ring-bg)" stroke-width="13"/></svg>
      <div class="ring-value" style="color:var(--muted)">0%</div><div class="ring-sub">Progress</div>
      <div class="ring-label">Unvisited</div>
    </div>
    <div class="ring" style="left:602px">
      <svg width="124" height="124" viewBox="0 0 124 124"><circle cx="62" cy="62" r="54" fill="none" stroke="var(--ring-bg)" stroke-width="13"/></svg>
      <div class="ring-value" style="color:var(--muted)">0%</div><div class="ring-sub">Progress</div>
      <div class="ring-label">Unvisited</div>
    </div>
  </div>
  <div class="abs current-word">Grab <svg width="15" height="15" viewBox="0 0 24 24"><path d="m12 2 3 6.5 7 .8-5.2 4.8 1.5 7L12 17.6 5.7 21.1l1.5-7L2 9.3l7-.8z" fill="#f5c518"/></svg></div>
  <div class="abs start-btn"><svg width="10" height="11" viewBox="0 0 10 11"><path d="M1 1v9l8-4.5z" fill="#fff"/></svg>Start Vocabulary Review Exercise 3</div>

  <div class="card" style="left:271px;top:416px;width:905px;height:124px">
    <div class="card-title" style="top:22px">Learning Curve Graph</div>
    <p class="card-copy" style="top:50px">The word "grab" is most commonly used as a verb, meaning to take something quickly or suddenly. Imagine you're running late for school. You don't have time for breakfast, so you quickly grab an apple from the kitchen and rush out the door. As you reach the bus stop, your friend waves and says, "Hey! Let's grab a coffee aller class" Later, when you sit down, your phone starts ringing. You grab it from your brag and answer.</p>
  </div>

  <div class="card" style="left:271px;top:561px;width:905px;height:315px">
    <div class="card-title" style="top:22px">Learning Curve Graph</div>
    <div class="curve-chart">
      <div class="band" style="top:0;height:53px;background:var(--band-1)">Long-Term Memory</div>
      <div class="band" style="top:53px;height:82px;background:var(--band-2)">Working Memory</div>
      <div class="band" style="top:135px;height:28px;background:var(--band-3)">Short-Term Memory</div>
      <div class="band" style="top:163px;height:30px;background:var(--band-4)">Forgotten Memory</div>
      <svg class="abs" style="left:0;top:0" width="869" height="193" viewBox="0 0 869 193"><path d="M211 56C300 50 377 100 377 193M132 132C175 128 198 160 200 193" fill="none" stroke="#2b3b47" stroke-width="1" stroke-dasharray="3 3"/><line x1="0" y1="193" x2="869" y2="193" stroke="#c8d3da"/></svg>
      <div class="bar" style="left:123px;height:63px"></div>
      <div class="bar" style="left:203px;height:135px"></div>
      <div class="tag" style="left:85px;top:123px">May 18</div>
      <div class="tag" style="left:160px;top:51px">May 19</div>
    </div>
    <div class="axis"><span>18 May</span><span>12:00</span><span>19 May</span><span>12:00</span><span>20 May</span><span>12:00</span><span>21 May</span><span>12:00</span><span>22 May</span><span>12:00</span><span>23 May</span><span>12:00</span><span>24 May</span><span>12:00</span><span>25 May</span><span>12:00</span><span>26 May</span><span>12:00</span><span>27 May</span><span>12:00</span><span>28 …</span></div>
    <div class="axis-title">Date Range</div>
    <div class="chart-credit">ChartKit.io</div>
  </div>

  <div class="card" style="left:271px;top:896px;width:905px;height:140px">
    <div class="card-title" style="top:22px">Word Mentor Learning Analysis</div>
    <p class="card-copy" style="top:50px;right:100px">Lorem ipsum dolor sit amet, consectetur adipiscing elit, sed do eiusmod tempor incididunt ut labore et dolore magna aliqua. Ut enim ad minim veniam, quis nostrud exercitation ullamco laboris nisi ut aliquip ex ea commodo consequat. Duis aute irure dolor in reprehenderit in voluptate velit esse cillum dolore eu fugiat nulla pariatur. Excepteur sint occaecat cupidatat non proident, sunt in culpa qui officia deserunt mollit anim id est laborum.</p>
  </div>

  <div class="abs veil"></div>

  <div class="abs vocab-popup">
    <div class="popup-select">All <svg width="9" height="6" viewBox="0 0 9 6"><path d="m1 1 3.5 3.5L8 1" stroke="#333" fill="none" stroke-width="1.3"/></svg></div>
    <svg class="popup-close" width="12" height="12" viewBox="0 0 12 12"><path d="m1 1 10 10M11 1 1 11" stroke="#333" stroke-width="1.4"/></svg>
    <div class="popup-group" style="top:66px"><svg width="18" height="18" viewBox="0 0 18 18"><circle cx="9" cy="10" r="6.5" stroke="#10a393" fill="none" stroke-width="1.4"/><path d="M9 6v4l3 2M7 1h4" stroke="#10a393" fill="none" stroke-width="1.4"/></svg>Short-Term Memory</div>
    <div class="popup-word" style="top:151px;top:151px;color:var(--teal);top:151px"></div>
    <div class="popup-word" style="top:150px"></div>
    <div class="popup-word" style="top:151px"></div>
    <div class="popup-word word--active" style="top:151px;top:151px"></div>
    <div class="popup-word" style="top:151px"></div>
    <div class="popup-word" style="top:151px;color:var(--teal);font-weight:700;top:151px"></div>
    <div class="popup-word" style="top:90px;color:var(--teal);font-weight:700">Grab</div>
    <div class="popup-group" style="top:109px"><svg width="18" height="18" viewBox="0 0 18 18"><rect x="4" y="4" width="10" height="10" stroke="#10a393" fill="none" stroke-width="1.4"/><rect x="7" y="7" width="4" height="4" fill="#10a393"/><path d="M7 1v3M11 1v3M7 14v3M11 14v3M1 7h3M1 11h3M14 7h3M14 11h3" stroke="#10a393" stroke-width="1.2"/></svg>Working Memory</div>
    <div class="popup-row" style="top:136px"><span>Cool Down</span><span>Crave</span><span>Go For</span><span>Go-To</span><span>In The Mood For</span><span>Sip</span><span>Soothing</span><span>Stick With</span><span>Throw In/Throw On</span></div>
    <div class="popup-group" style="top:156px"><svg width="16" height="18" viewBox="0 0 16 18"><rect x="2" y="8" width="12" height="9" rx="1.5" stroke="#10a393" fill="none" stroke-width="1.4"/><path d="M5 8V5a3 3 0 0 1 6 0" stroke="#10a393" fill="none" stroke-width="1.4"/></svg>Long-Term Memory <span class="popup-help">?</span></div>
    <div class="popup-word" style="top:182px">Give It A Try</div>
  </div>
</section>

</body>
</html>
```